e-commerce store for sport clothing online store "baseball merchandise "web application...

I want to design a UX/UI for my web application website for the online store I will provide you with the following:
1. screen shots of the initial design for the pages>
2. the logo files.
3. The brand guideline file.

the provided files (screen shots) is guideline I want to see CREATIVITY with the UX/UI DESIGN.
PS. PLEASE FOLLOW THE BRANDGUIDE LINE CAREFULLY SPECIALLY THE TYPOGRAPHY & THE COLOR CODES.

PLEASE VISIT THIS WEBSITE brightlane.varomi-qz.com to see more for the screens.

```html
<!DOCTYPE html>
<html lang="en">
<head>
<meta charset="utf-8">
<title>Checkout – Order Confirmation</title>
<link rel="stylesheet" href="https://fonts.googleapis.com/css2?family=Lato:wght@400;700;900&display=swap">
<style>
  :root {
    --navy: #0f2347;
    --ink: #111111;
    --page: #ffffff;
    --muted-line: #d9d9d9;
    --success: #2bb24c;
    --scrim: rgba(0, 0, 0, 0.2);
    --white: #ffffff;
    --black: #000000;
  }
  * { box-sizing: border-box; margin: 0; padding: 0; }
  html, body {
    width: 1200px; height: 2667px; overflow: hidden;
    background: var(--page);
    font-family: "Lato", sans-serif;
    color: var(--ink);
  }
  .screen {
    position: absolute; left: 0; top: 0;
    width: 360px; height: 800px;
    transform: scale(3.33334);
    transform-origin: 0 0;
    background: var(--page);
    overflow: hidden;
  }
  .app-header {
    position: absolute; left: 0; top: 0; width: 360px; height: 82px;
    background: var(--navy);
  }
  .app-header .back { position: absolute; left: 22px; top: 31px; }
  .app-header h1 {
    position: absolute; left: 0; right: 0; top: 30px;
    text-align: center; font-size: 17px; font-weight: 700; color: var(--white);
  }
  .stepper { position: absolute; left: 0; top: 118px; width: 360px; height: 80px; }
  .stepper .track {
    position: absolute; left: 80px; width: 203px; top: 19px; height: 1.5px; background: var(--navy);
  }
  .step { position: absolute; width: 90px; margin-left: -45px; text-align: center; }
  .step .dot {
    width: 40px; height: 40px; border-radius: 50%; margin: 0 auto;
    background: var(--navy); color: var(--white);
    font-weight: 900; font-size: 20px; line-height: 40px;
  }
  .step .label { font-size: 12px; line-height: 15px; margin-top: 4px; }
  .items-title { position: absolute; left: 14px; top: 221px; font-size: 15px; font-weight: 700; }
  .item { position: absolute; left: 14px; width: 332px; height: 66px; }
  .item .thumb { position: absolute; left: 0; top: 0; width: 55px; height: 66px; border-radius: 3px; }
  .item .price { position: absolute; right: 0; top: 6px; font-size: 13px; font-weight: 700; }
  .thumb.shirt { background: linear-gradient(160deg, #52b88f, #3f9a74); }
  .thumb.cap { background: linear-gradient(160deg, #f4f4f4, #b9bcc0); border: 1px solid var(--muted-line); }
  .summary { position: absolute; left: 20px; width: 320px; top: 623px; font-size: 13px; }
  .summary .row { display: flex; justify-content: space-between; height: 27px; }
  .summary .row span:last-child { font-weight: 700; }
  .checkout-bar {
    position: absolute; left: 5px; right: 5px; top: 742px; height: 62px;
    background: var(--white); border-radius: 10px;
    box-shadow: 0 -1px 4px rgba(0,0,0,0.12);
  }
  .place-order {
    position: absolute; left: 7px; right: 7px; top: 6px; height: 44px;
    background: var(--black); color: var(--white); border-radius: 6px;
    font-size: 14px; font-weight: 700; text-align: center; line-height: 44px;
  }
  .scrim { position: absolute; inset: 0; background: var(--scrim); }
  .modal {
    position: absolute; left: 40px; top: 232px; width: 279px; height: 372px;
    background: var(--white); border-radius: 4px; text-align: center;
  }
  .modal .close { position: absolute; right: 12px; top: 11px; }
  .modal .badge { position: absolute; left: 104px; top: 54px; }
  .modal h2 { position: absolute; left: 0; right: 0; top: 148px; font-size: 20px; font-weight: 700; }
  .modal .message { position: absolute; left: 50px; right: 50px; top: 179px; font-size: 13px; line-height: 17px; }
  .modal .order-number { position: absolute; left: 0; right: 0; top: 251px; font-size: 13px; }
  .modal .continue {
    position: absolute; left: 54px; top: 308px; width: 172px; height: 43px;
    background: var(--navy); color: var(--white); border-radius: 4px;
    font-size: 14px; font-weight: 700; line-height: 43px;
  }
</style>
</head>
<body>
<div class="screen">
  <header class="app-header">
    <svg class="back" width="20" height="20" viewBox="0 0 20 20" fill="none" stroke="#ffffff" stroke-width="2" stroke-linecap="round" stroke-linejoin="round"><path d="M17 10H3M9 4l-6 6 6 6"/></svg>
    <h1>Checkout</h1>
  </header>

  <div class="stepper">
    <div class="track"></div>
    <div class="step" style="left:80px"><div class="dot">1</div><div class="label">Shipping<br>Details</div></div>
    <div class="step" style="left:180px"><div class="dot">2</div><div class="label">Payment<br>Details</div></div>
    <div class="step" style="left:283px"><div class="dot">3</div><div class="label">Confirmation</div></div>
  </div>

  <div class="items-title">Items</div>
  <div class="item" style="top:257px">
    <div class="thumb shirt" role="img" aria-label="Green sport shirt product photo"></div>
    <div class="price">24.000 KD</div>
  </div>
  <div class="item" style="top:355px">
    <div class="thumb cap" role="img" aria-label="Grey baseball cap product photo"></div>
    <div class="price">25.000 KD</div>
  </div>

  <div class="summary">
    <div class="row"><span>Subtotal</span><span>49.000 KD</span></div>
    <div class="row"><span>Delivery Charge</span><span>1.000 KD</span></div>
    <div class="row"><span>Total</span><span>50.000 KD</span></div>
  </div>

  <div class="checkout-bar"><div class="place-order">Place Order</div></div>

  <div class="scrim"></div>

  <div class="modal" role="dialog" aria-label="Order confirmation">
    <svg class="close" width="14" height="14" viewBox="0 0 14 14" stroke="#0f2347" stroke-width="2.2" stroke-linecap="round"><path d="M2 2l10 10M12 2L2 12"/></svg>
    <svg class="badge" width="71" height="71" viewBox="0 0 71 71">
      <circle cx="35.5" cy="35.5" r="35.5" fill="#2bb24c"/>
      <path d="M19 37l11 11 23-24" fill="none" stroke="#ffffff" stroke-width="7" stroke-linecap="round" stroke-linejoin="round"/>
    </svg>
    <h2>Confirmation</h2>
    <p class="message">Your order has been placed successfully!</p>
    <p class="order-number">Order number is: 1223</p>
    <div class="continue">Continue Shopping</div>
  </div>
</div>
</body>
</html>
```